Clear Plastic Card Design

I am looking to have a business card designed from my logo icon. I am looking to match the style of a different business card I have attached in the files.
Looking for a card that is plastic, with layers of transparency in the shape of my logo icon (also attached in the files) - not a circle like the other card. The winning design will incorporate the red icon logo on the front and back and include the charity's name, "Light for the Weary Souls" in the same or similar font, as well as an email and phone number. For now, use the email: email@lightfortheweary-mail.org and the phone number 555-382-7194.
We like how the sample business card has transparency, partial and full opacity layers and a matching color scheme. Files will need to be in vector so that our business card printing company can work with it.
UPDATE:
We've some excellent designs in, thank you everyone! I got an early review from the owner, and he requested a minor redirect to find his perfect design. He wants the design to stand out by NOT being a rectangle. Try instead a circle, square, or best yet - something that falls in the outline of the logo icon, either fully or partially. Thank you, everyone!
Light for the Weary Souls text should be incorporated as well as a phone and email.

```html
<!DOCTYPE html>
<html lang="en">
<head>
<meta charset="utf-8">
<title>Light for the Weary Souls – Die-cut Business Card</title>
<link rel="stylesheet" href="https://fonts.googleapis.com/css2?family=Lexend:wght@300&family=Montserrat:wght@400;700&display=swap">
<style>
  :root {
    --backdrop: #e4e4e4;
    --brand-red: #d02027;
    --brand-red-dark: #b51b22;
    --card-white: #ffffff;
    --card-shadow: #cfcfcf;
    --ink: #1e1e1e;
  }
  * { margin: 0; padding: 0; box-sizing: border-box; }
  html, body { width: 1200px; height: 1200px; overflow: hidden; }
  body { background: var(--backdrop); position: relative; }

  .card { position: absolute; left: 0; width: 1200px; }
  .card-shape { position: absolute; left: 0; top: 0; }

  .card-front { top: 0; height: 600px; }
  .front-fill { fill: var(--brand-red); }
  .front-edge { fill: var(--brand-red-dark); }
  .mark-area { fill: var(--card-white); }
  .front-name {
    position: absolute; left: 226px; top: 370px;
    font-family: "Lexend", sans-serif; font-weight: 300;
    font-size: 62px; line-height: 72px; color: var(--card-white);
    letter-spacing: 0.3px;
  }

  .card-back { top: 600px; height: 600px; }
  .back-fill { fill: var(--card-white); }
  .back-shadow { fill: var(--card-shadow); }
  .back-name {
    position: absolute; right: 276px; top: 168px; text-align: right;
    font-family: "Montserrat", sans-serif; font-weight: 700;
    font-size: 33px; line-height: 46px; color: var(--brand-red);
    letter-spacing: 0.5px;
  }
  .contact-list { position: absolute; right: 270px; top: 310px; list-style: none; }
  .contact-item {
    display: flex; justify-content: flex-end; align-items: center; gap: 22px;
    font-family: "Montserrat", sans-serif; font-weight: 400;
    font-size: 26px; line-height: 42px; color: var(--ink);
  }
  .contact-icon { width: 20px; height: 20px; fill: var(--brand-red); flex: none; }
</style>
</head>
<body>

<section class="card card-front" aria-label="Card front">
  <svg class="card-shape" width="1200" height="600" viewBox="0 0 1200 600">
    <g class="front-edge">
      <rect x="667" y="54" width="141" height="96" rx="30"/>
      <rect x="504" y="98" width="524" height="360" rx="56"/>
      <rect x="167" y="317" width="541" height="247" rx="34"/>
      <rect x="672" y="422" width="136" height="161" rx="30"/>
    </g>
    <g class="front-fill">
      <rect x="675" y="62" width="125" height="80" rx="24"/>
      <rect x="512" y="106" width="508" height="344" rx="50"/>
      <rect x="175" y="325" width="525" height="231" rx="28"/>
      <rect x="680" y="430" width="120" height="145" rx="24"/>
    </g>
    <rect class="mark-area" x="730" y="150" width="240" height="240" role="img" aria-label="Logo mark area"/>
  </svg>
  <p class="front-name">Light for the<br>Weary Souls</p>
</section>

<section class="card card-back" aria-label="Card back">
  <svg class="card-shape" width="1200" height="600" viewBox="0 0 1200 600">
    <g class="back-shadow">
      <rect x="676" y="28" width="130" height="80" rx="24"/>
      <rect x="518" y="78" width="508" height="350" rx="50"/>
      <rect x="186" y="296" width="595" height="218" rx="28"/>
      <rect x="668" y="428" width="113" height="105" rx="24"/>
    </g>
    <g class="back-fill">
      <rect x="670" y="20" width="130" height="80" rx="24"/>
      <rect x="512" y="70" width="508" height="350" rx="50"/>
      <rect x="180" y="288" width="595" height="218" rx="28"/>
      <rect x="662" y="420" width="113" height="105" rx="24"/>
    </g>
  </svg>
  <h1 class="back-name">LIGHT FOR THE<br>WEARY SOULS</h1>
  <ul class="contact-list">
    <li class="contact-item">
      <span>555-382-7194</span>
      <svg class="contact-icon" viewBox="0 0 24 24" aria-hidden="true"><path d="M6.6 10.8a15.2 15.2 0 0 0 6.6 6.6l2.2-2.2a1 1 0 0 1 1-.25 11.4 11.4 0 0 0 3.6.57 1 1 0 0 1 1 1V20a1 1 0 0 1-1 1A17 17 0 0 1 3 4a1 1 0 0 1 1-1h3.5a1 1 0 0 1 1 1c0 1.25.2 2.450.57 3.57a1 1 0 0 1-.25 1z"/></svg>
    </li>
    <li class="contact-item">
      <span>email@lightfortheweary-mail.org</span>
      <svg class="contact-icon" viewBox="0 0 24 24" aria-hidden="true"><path d="M3 5h18a1 1 0 0 1 1 1v12a1 1 0 0 1-1 1H3a1 1 0 0 1-1-1V6a1 1 0 0 1 1-1zm9 7.2L20 7H4z"/></svg>
    </li>
  </ul>
</section>

</body>
</html>
```